Design eines Hausetiketts für traditionelles Weingut
Zielgruppe
Wir das Familienweingut Brandauer in Gimbsheim/Rheinhessen sind ein traditionelles Weingut das seine Reben selbst kultiviert und die Weine auch selbst ausbaut. Wir haben jeden Schritt in der Weinherstellung selbst in der Hand und vermarkten den Wein dann an unsere Privatkunden. Unsere Kundenstruktur sieht folgendermaßen aus: Wir haben 100% Privatkunden die unseren Wein konsumieren. Da jetzt die nächste Generation in den Weinbaubetrieb einsteigt und auch Ideen hat möchten wir ein Hausetikett einführen. Im Moment haben wir noch sehr viele unterschiedliche Etiketten und kein Hausetikett. Da die Verlagsetiketten immer seltener zu unseren Vorstellungen passen, möchten wir hier auf diesem Wege ein Hausetikett anfertigen lassen. Generell möchten wir unseren Außenauftritt komplett modernisieren. Sie können sich über die Vielfalt in unserem Betrieb unter www.weingut-brandauer-beispiel.de einen Überblick verschaffen. Langfristig gesehen wollen wir aber unsere Weinkarte verkleinern.
Aufgabenstellung
Wir haben uns vor ca. 1,5 Jahren hier auf dieser Website bereits ein Logo designen lassen. Es wäre schön wenn man das Logo bei den Entwürfen für die Etiketten berücksichtigen würde. Das wäre aber KEIN MUSS. Auch wäre es gut wenn man das ,,Wein' bei unserem Namen weglassen könnte.
Das Etikett sollte aus Vorder-und Rückenetikett bestehen und edel wirken. Vorne sollte die Rebsorte und die Geschmacksangabe stehen. Der Rest sollte auf das Rückenetikett.
Das Vorderetikett sollte ein richtiger Eyecatcher sein und im Supermarkt z.B. aus vielen anderen herausstechen. Das wäre ganz wichtig.
Man kann bei den Farben unterscheiden in 3 Konzepte.
Literwein als einsteiger Wein
Dann die Gutsweine und zum Schluss die Lagenweine. Alles Farblich oder im design etwas abgesetzt.

```html
<!DOCTYPE html>
<html lang="de">
<head>
<meta charset="utf-8">
<title>Brandauer Silvaner Weisswein – Vorderetikett</title>
<link rel="stylesheet" href="https://fonts.googleapis.com/css2?family=Cinzel:wght@400&family=Great+Vibes&family=Oswald:wght@600&display=swap">
<style>
  :root {
    --stage: #9a918c;
    --paper: #ececec;
    --paper-shade: #dcdcdc;
    --ink-grey: #8a8a8a;
    --gold-dark: #b68f4e;
    --gold-mid: #d9b27a;
    --gold-light: #f0cfa6;
    --script-white: #ffffff;
    --script-soft: #e4e4e4;
    --land-light: #cfcfcf;
    --land-dark: #9e9e9e;
  }
  * { margin: 0; padding: 0; box-sizing: border-box; }
  html, body {
    width: 1200px;
    height: 800px;
    overflow: hidden;
    background: var(--stage);
  }
  .canvas {
    position: relative;
    width: 1200px;
    height: 800px;
    display: flex;
    align-items: center;
    justify-content: center;
  }
  .front-label {
    position: relative;
    width: 540px;
    height: 720px;
    background: radial-gradient(ellipse at 45% 30%, #f6f6f6 0%, var(--paper) 55%, var(--paper-shade) 100%);
    overflow: hidden;
    box-shadow: 0 6px 24px rgba(0,0,0,0.25);
  }
  .vineyard-landscape {
    position: absolute;
    left: 0;
    right: 0;
    bottom: 0;
    height: 330px;
    background: linear-gradient(180deg, rgba(207,207,207,0) 0%, var(--land-light) 30%, #b9b9b9 55%, var(--land-dark) 100%);
  }
  .winery-name {
    position: absolute;
    top: 118px;
    left: 0;
    right: 0;
    display: flex;
    align-items: center;
    justify-content: center;
    gap: 12px;
    font-family: 'Cinzel', serif;
    font-size: 30px;
    line-height: 1;
    letter-spacing: 1px;
    color: var(--ink-grey);
  }
  .winery-name .mark {
    width: 14px;
    height: 14px;
    border-radius: 50%;
    background: var(--ink-grey);
  }
  .grape-variety {
    position: absolute;
    left: 140px;
    bottom: 100px;
    writing-mode: vertical-rl;
    transform: rotate(180deg);
    font-family: 'Oswald', sans-serif;
    font-weight: 600;
    font-size: 108px;
    line-height: 1;
    letter-spacing: 1px;
    background: linear-gradient(100deg, var(--gold-dark) 0%, var(--gold-mid) 35%, var(--gold-light) 50%, var(--gold-mid) 65%, var(--gold-dark) 100%);
    -webkit-background-clip: text;
    background-clip: text;
    color: transparent;
  }
  .wine-style {
    position: absolute;
    left: 190px;
    top: 318px;
    font-family: 'Great Vibes', cursive;
    font-size: 60px;
    line-height: 1;
    white-space: nowrap;
    transform: rotate(6deg);
    text-shadow: 0 1px 3px rgba(0,0,0,0.18);
  }
  .wine-style .lead { color: var(--script-white); }
  .wine-style .tail { color: var(--script-soft); }
</style>
</head>
<body>
  <main class="canvas">
    <section class="front-label">
      <div class="vineyard-landscape" role="img" aria-label="Weinberglandschaft in Grautönen mit sanften Hügeln und Rebzeilen"></div>
      <div class="winery-name"><span class="mark"></span><span>BRANDAUER</span></div>
      <h1 class="grape-variety">SILVANER</h1>
      <p class="wine-style"><span class="lead">Weiss</span><span class="tail">wein</span></p>
    </section>
  </main>
</body>
</html>
```